I need a business card for my original fine art pieces

I would like a business card design including a logo design for a new business in the art world. I am based in the Hunter Valley NSW Australia. I am a contemporary figurative, encaustic and wildlife artist. I would like to be able to upload my email and mobile number to this as well. This design should be one that I can incorporate into banners and flyers etc. Id like to incorporate one of my own images or partial image into the background or somewhere below. My initials are RJ and I would like these used as a logo type. I would like the use of some colour and it to be bright and catchy. The final design should communicate artwork custom made and commissions available.

Overview: Original Fine Artworks for sale, online, art galleries etc, Custom made to order and by commission.

Target market is world wide audience and corporate world

My figurative work is painted using acrylics in a lot of natural ochre colours that reflect the Australian Outback, on canvas, linen, paper or board: My encaustic work is created in a contemporary abstract style using a blow torch and a made with a medium of 100% pure bees wax, Damar resin, mixed media and coloured pigments, applied to Birch board. My wildlife are created using coloured pencil and mixed media on a variety of paper types or board.

```html
<!DOCTYPE html>
<html lang="en">
<head>
<meta charset="utf-8">
<title>Rhea Jarvis – Business Card</title>
<link rel="stylesheet" href="https://fonts.googleapis.com/css2?family=Open+Sans:wght@400;600&display=swap">
<style>
  :root {
    --stage: #2a2a2a;
    --card-black: #1c1c1e;
    --accent: #ea4f0c;
    --white: #ffffff;
    --card-w: 520px;
    --card-h: 300px;
  }
  * { box-sizing: border-box; margin: 0; padding: 0; }
  html, body { width: 1200px; height: 900px; overflow: hidden; }
  body {
    background: var(--stage);
    font-family: "Open Sans", Arial, sans-serif;
    position: relative;
  }
  .card {
    position: absolute;
    top: 300px;
    width: var(--card-w);
    height: var(--card-h);
    border-radius: 18px;
    overflow: hidden;
    background: var(--card-black);
    box-shadow: 0 8px 24px rgba(0,0,0,0.45);
  }
  .card--front { left: 70px; }
  .card--back { left: 610px; }
  .card__split { position: absolute; inset: 0; }

  /* Front: contact side */
  .contact-person { position: absolute; left: 30px; top: 78px; }
  .contact-person__name {
    color: var(--accent); font-weight: 600; font-size: 19px; letter-spacing: 0.5px;
  }
  .contact-person__role {
    color: var(--white); font-size: 11px; letter-spacing: 0.6px; margin-top: -2px;
  }
  .contact-list { position: absolute; left: 30px; top: 140px; list-style: none; }
  .contact-list li {
    display: flex; align-items: center; gap: 8px;
    color: var(--white); font-size: 12.5px; line-height: 19px;
  }
  .contact-list svg { width: 9px; height: 9px; fill: var(--accent); flex: none; }
  .contact-address {
    position: absolute; left: 30px; top: 222px;
    color: var(--white); font-size: 12.5px; line-height: 18px;
  }

  /* Brand lockup */
  .brand {
    position: absolute; display: flex; flex-direction: column; align-items: center;
  }
  .brand__mark {
    width: 78px; height: 78px; border-radius: 50%;
    border: 3px solid var(--white);
  }
  .brand__name {
    font-weight: 600; font-size: 25px; letter-spacing: 2px;
    text-transform: uppercase; margin-top: 10px; line-height: 1;
  }
  .brand__tagline {
    font-size: 11px; letter-spacing: 2.4px; text-transform: uppercase; margin-top: 4px;
  }
  .card--front .brand { left: 250px; width: 270px; top: 60px; }
  .card--front .brand__name,
  .card--front .brand__tagline { color: var(--white); }
  .card--back .brand { left: 0; right: 0; top: 62px; }
  .card--back .brand__mark { border-color: var(--accent); }
  .card--back .brand__name { color: var(--accent); }
  .card--back .brand__tagline { color: var(--white); }
</style>
</head>
<body>

  <section class="card card--front">
    <svg class="card__split" viewBox="0 0 520 300" preserveAspectRatio="none" aria-hidden="true">
      <rect width="520" height="300" fill="var(--accent)"/>
      <polygon points="0,0 150,0 225,100 235,300 0,300" fill="var(--card-black)"/>
    </svg>

    <div class="contact-person">
      <p class="contact-person__name">LIAM CARTER</p>
      <p class="contact-person__role">GENERAL MANAGER</p>
    </div>

    <ul class="contact-list">
      <li><svg viewBox="0 0 10 10"><path d="M2 0.5 L3.6 2.6 L2.8 3.6 Q4 6 6.4 7.2 L7.4 6.4 L9.5 8 L8.2 9.5 Q1.5 8 0.5 1.8 Z"/></svg>(403) 555-0182</li>
      <li><svg viewBox="0 0 10 10"><rect x="0.5" y="2" width="9" height="6"/></svg>hello@rheajarvis.com</li>
      <li><svg viewBox="0 0 10 10"><circle cx="5" cy="5" r="4.5"/></svg>www.rheajarvisart.com</li>
    </ul>

    <p class="contact-address">42 Vineyard Road,<br>Pokolbin, NSW 2320</p>

    <div class="brand">
      <div class="brand__mark"></div>
      <p class="brand__name">Rhea Jarvis</p>
      <p class="brand__tagline">Original Fine Artworks</p>
    </div>
  </section>

  <section class="card card--back">
    <div class="brand">
      <div class="brand__mark"></div>
      <p class="brand__name">Rhea Jarvis</p>
      <p class="brand__tagline">Original Fine Artworks</p>
    </div>
  </section>

</body>
</html>
```